Letterhead for Business Law Firm

We need a letter head for our firm based on the design we have settled on and it is attached. Our clients are small and large businesses around the world, and our letterhead is used typically for formal legal purposes such as demand letters (accusing the recipient of doing bad things) or responding to demand letters. It may also be sent to regulators and other government agencies. So this needs to be tasteful, but a little edgy as well - we try to convey that we are a firm that is different - businesses and investors come to us for creative, quick advice, typically in high stress circumstances, and for our ability to work through high conflict situations, and rapid paced engagements.

Target Market(s)

Lawyers, business executives, investors, government regulators who may receive letters from this firm on behalf of its clients.

Industry/Entity Type

Business

Requirements
Must have
• The design and the firm's contact information:
• Thornwell Law Firm, P.C.
• 1876 NE 57th Ave
• Portland, OR 97213
• phone: 971 555 0147
• fax: 971 555 0182
• in what placement and how depicted (e.g. a phone icon instead of the word "phone") I leave to your creative ideas.
Nice to have
• design and information can be placed at the top, bottom and/or sides of the letter, and the design should be for a standard letter size paper - and can have a separate design for the second page.

```html
<!DOCTYPE html>
<html lang="en">
<head>
<meta charset="utf-8">
<title>Thornwell Law Firm, P.C. — Letterhead</title>
<link rel="stylesheet" href="https://fonts.googleapis.com/css2?family=Josefin+Sans:wght@300&family=Open+Sans:wght@400&display=swap">
<style>
  :root {
    --paper: #ffffff;
    --ink: #1b1719;
    --teal: #3f7b80;
    --footer-text: #ffffff;
  }
  * { margin: 0; padding: 0; box-sizing: border-box; }
  html, body {
    width: 1019px;
    height: 1200px;
    overflow: hidden;
    background: var(--paper);
  }
  .letterhead {
    position: relative;
    width: 1019px;
    height: 1200px;
    background: var(--paper);
  }
  .brand {
    position: absolute;
    top: 68px;
    left: 0;
    width: 100%;
    text-align: center;
    font-family: "Josefin Sans", sans-serif;
    font-weight: 300;
    font-size: 50px;
    letter-spacing: 14px;
    color: var(--ink);
    padding-left: 14px;
  }
  .footer-band {
    position: absolute;
    left: 0;
    bottom: 0;
    width: 1019px;
    height: 200px;
  }
  .footer-address,
  .footer-contacts {
    position: absolute;
    left: 0;
    width: 100%;
    text-align: center;
    font-family: "Open Sans", sans-serif;
    color: var(--footer-text);
    white-space: nowrap;
  }
  .footer-address {
    top: 1131px;
    font-size: 14px;
    letter-spacing: 1.6px;
  }
  .footer-contacts {
    top: 1160px;
    font-size: 14px;
    display: flex;
    justify-content: center;
    gap: 14px;
  }
  .contact-item {
    display: inline-flex;
    align-items: center;
    gap: 4px;
  }
  .contact-icon {
    width: 11px;
    height: 11px;
    fill: var(--footer-text);
  }
</style>
</head>
<body>
<main class="letterhead">
  <h1 class="brand">THORNWELL</h1>

  <svg class="footer-band" viewBox="0 1000 1019 200" preserveAspectRatio="none" aria-hidden="true">
    <path d="M0 1162 Q509.5 1030 1019 1162 L1019 1166 Q509.5 1050 0 1166 Z" fill="var(--teal)"/>
    <path d="M0 1166 Q509.5 1055 1019 1166 L1019 1200 L0 1200 Z" fill="var(--ink)"/>
  </svg>

  <p class="footer-address">1876 NE 57th Ave, Portland, OR 97213</p>

  <p class="footer-contacts">
    <span class="contact-item">
      <svg class="contact-icon" viewBox="0 0 12 12" aria-label="Phone" role="img"><path d="M3 1 L5 3.5 L4 5 Q5 7 7 8 L8.5 7 L11 9 L9.5 11 Q5 11 2.5 8 Q0.5 5 1 2.5 Z"/></svg>
      971 555 0147
    </span>
    <span class="contact-item">
      <svg class="contact-icon" viewBox="0 0 12 12" aria-label="Fax" role="img"><rect x="3" y="1" width="6" height="4"/><rect x="1" y="5" width="10" height="5" rx="1"/><rect x="3" y="8" width="6" height="3"/></svg>
      971 555 0182
    </span>
    <span class="contact-item">
      <svg class="contact-icon" viewBox="0 0 12 12" aria-label="Email" role="img"><path d="M1 4 L6 1 L11 4 L11 11 L1 11 Z M2 5 L6 8 L10 5 L10 10 L2 10 Z" fill-rule="evenodd"/></svg>
      info@thornwelllaw.com
    </span>
    <span class="contact-item">
      <svg class="contact-icon" viewBox="0 0 12 12" aria-label="Website" role="img"><path d="M6 0.5 A5.5 5.5 0 1 0 6 11.5 A5.5 5.5 0 1 0 6 0.5 Z M6 1.7 A4.3 4.3 0 1 1 6 10.3 A4.3 4.3 0 1 1 6 1.7 Z M1.5 5.5 H10.5 V6.5 H1.5 Z M5.5 1 H6.5 V11 H5.5 Z"/></svg>
      www.thornwelllaw.com
    </span>
  </p>
</main>
</body>
</html>
```